I need a label design to go on our jars of honey. Our company is called Marrowdale Honey Co. The type of honey is called Fernlight Glen Honey. The jars are 1kg. Attached is the label size. Left hand side needs to have nutritional info... as attached. Middle section is our company name, honey type, 1kg & Whangamata, NZ. Right hand side needs to have info as per photo (raw honey etc). I would like to upload more pictures... but I’m unsure how to do this? Thanks, Carla

Target Market(s)

Honey consumers... families

Industry/Entity Type

Food Production

Colors

Designer to choose colors to be used in the design.

Requirements
Must have
• Nutritional info as per upload
• Type of honey & company name as per upload
• 1kg
• Address
Nice to have
• Similar fonts to upload.
• Possibly background image... floral or beach... very faint though.

```html
<!DOCTYPE html>
<html lang="en">
<head>
<meta charset="utf-8">
<title>Marrowdale Honey Co. – Fernlight Glen Honey Label</title>
<link rel="stylesheet" href="https://fonts.googleapis.com/css2?family=Amatic+SC:wght@400&family=Raleway:wght@300&family=Nothing+You+Could+Do&display=swap">
<style>
  :root {
    --backdrop: #1f2224;
    --label-light: #c56c52;
    --label-mid: #b45f48;
    --label-dark: #9a4a39;
    --bloom: rgba(236, 178, 160, 0.32);
    --ink: #f1e9e5;
    --ink-soft: #e4d6d0;
    --rule: #f4ece8;
  }
  html, body {
    margin: 0;
    padding: 0;
    width: 1200px;
    height: 1200px;
    overflow: hidden;
    background: var(--backdrop);
  }
  .label {
    position: absolute;
    left: 40px;
    top: 208px;
    width: 1120px;
    height: 785px;
    overflow: hidden;
    background: linear-gradient(90deg, var(--label-light) 0%, var(--label-mid) 55%, var(--label-dark) 100%);
  }
  .floral-backdrop {
    position: absolute;
    inset: 0;
    background:
      radial-gradient(circle at 560px 170px, var(--bloom) 0, transparent 150px),
      radial-gradient(circle at 900px 440px, var(--bloom) 0, transparent 170px),
      radial-gradient(circle at 470px 560px, var(--bloom) 0, transparent 160px),
      radial-gradient(circle at 740px 80px, rgba(236,178,160,0.2) 0, transparent 130px);
  }

  /* Nutrition panel */
  .nutrition-panel {
    position: absolute;
    left: 24px;
    top: 67px;
    width: 236px;
    color: var(--ink);
    font-family: Arial, Helvetica, sans-serif;
  }
  .nutrition-table {
    width: 100%;
    height: 469px;
    border: 2px solid var(--rule);
    border-collapse: collapse;
    font-size: 15px;
  }
  .nutrition-table caption {
    caption-side: top;
    text-align: left;
    font-size: 17px;
    font-weight: bold;
    padding-bottom: 6px;
  }
  .nutrition-table td,
  .nutrition-table th {
    padding: 3px 6px;
    text-align: left;
    font-weight: normal;
  }
  .nutrition-table td + td,
  .nutrition-table th + th { text-align: right; }
  .nutrition-table .row-rule td,
  .nutrition-table .row-rule th { border-bottom: 2px solid var(--rule); }
  .storage-note {
    margin: 22px 0 0;
    font-style: italic;
    font-size: 16px;
    line-height: 23px;
    text-align: right;
  }

  /* Front panel */
  .front-panel {
    position: absolute;
    left: 270px;
    top: 0;
    right: 0;
    bottom: 0;
    text-align: center;
    color: var(--ink);
  }
  .brand-name {
    position: absolute;
    left: 0; right: 0;
    top: 62px;
    margin: 0;
    font-family: "Amatic SC", sans-serif;
    font-weight: 400;
    font-size: 46px;
    letter-spacing: 0.32em;
    padding-left: 0.32em;
  }
  .honey-type {
    position: absolute;
    left: 0; right: 0;
    top: 290px;
    margin: 0;
    font-weight: normal;
  }
  .honey-type .variety {
    display: block;
    font-family: "Raleway", sans-serif;
    font-weight: 300;
    font-size: 42px;
    letter-spacing: 0.5em;
    padding-left: 0.5em;
    color: var(--ink-soft);
  }
  .honey-type .script {
    display: block;
    margin-top: -10px;
    font-family: "Nothing You Could Do", cursive;
    font-size: 100px;
    line-height: 1.2;
  }
  .net-weight {
    position: absolute;
    left: 0; right: 0;
    top: 598px;
    margin: 0;
    font-family: "Amatic SC", sans-serif;
    font-size: 46px;
    letter-spacing: 0.15em;
  }
  .divider {
    position: absolute;
    left: 50%;
    top: 676px;
    width: 50px;
    height: 3px;
    margin-left: -25px;
    background: var(--rule);
  }
  .origin {
    position: absolute;
    left: 0; right: 0;
    top: 706px;
    margin: 0;
    font-family: "Amatic SC", sans-serif;
    font-size: 46px;
    letter-spacing: 0.25em;
  }
</style>
</head>
<body>
  <div class="label">
    <div class="floral-backdrop" role="img" aria-label="Faint photograph of pale blossoms behind the label text"></div>

    <section class="nutrition-panel">
      <table class="nutrition-table">
        <caption>Nutrition Information</caption>
        <tr><td colspan="3">Servings per jar: 50</td></tr>
        <tr class="row-rule"><td colspan="3">Serving size: 20g</td></tr>
        <tr class="row-rule"><th></th><th>Per serve</th><th>Per 100g</th></tr>
        <tr><td>Energy</td><td>272kJ</td><td>1360kJ</td></tr>
        <tr><td>Protein</td><td>0.1g</td><td>0.4g</td></tr>
        <tr><td>Fat</td><td>0g</td><td>0g</td></tr>
        <tr><td>Carbohydrate</td><td>16.2g</td><td>81g</td></tr>
        <tr><td>Sugars</td><td>16.0g</td><td>80g</td></tr>
        <tr><td>Sodium</td><td>1mg</td><td>5mg</td></tr>
      </table>
      <p class="storage-note">Store below 25°C. Warm gently if crystallised, as needed. Best within 24 months.</p>
    </section>

    <div class="front-panel">
      <p class="brand-name">MARROWDALE HONEY CO.</p>
      <h1 class="honey-type">
        <span class="variety">FERNLIGHT</span>
        <span class="script">Glen Honey</span>
      </h1>
      <p class="net-weight">1kg</p>
      <span class="divider"></span>
      <p class="origin">TAREWA BAY, N.Z.</p>
    </div>
  </div>
</body>
</html>
```